Business card for Eyelash extension salon in Beverly Hills,California USA

We need new business card for our salon in Beverly Hills. The salon name is 'Lashvera' . We would like to have...Business name: Lashvera Name of person: will provide later Address 4720 N.Alder Crest Ave Beverly Hills , CA 90210 Phone: will provide later (Text only) Web: www.lashverastudio.example Snapgrid icon, Circlebook icon follow us for seasonal campaign and news @lashverastudiolounge Design should look elegant, high-end, clean, simple, cohesive with my brand. Please refer my brand board. Business name color will be metallic bronzy color. Im thinking grey background or white background. Thanks

Target Market(s)

25-35. Gender neutral. People who are in Entertainment business industry.
This is High-end Eyelash extension salon in Beverly Hills

Industry/Entity Type

Beauty Salon

Contact Information for Business Card

Business name: Lashvera
Name of person: will provide later
Address 4720 N.Alder Crest Ave Beverly Hills , CA 90210
Phone: will provide later (Text only)
Web: www.lashverastudio.example
Snapgrid icon, Circlebook icon
follow us for seasonal campaign and news @lashverastudiolounge

Requirements
Must have
• Beautiful, elegant, clean and simple look but very attractive and modern
Should not have
• We don't like too clutter, too busy designs.

```html
<!DOCTYPE html>
<html lang="en">
<head>
<meta charset="utf-8">
<title>Lashvera – Business Card</title>
<link rel="stylesheet" href="https://fonts.googleapis.com/css2?family=Playfair+Display:wght@400;700&family=Work+Sans:wght@400;500&display=swap">
<style>
  :root {
    --bronze: #8a6a52;
    --tan: #c9ab8c;
    --paper: #ffffff;
    --ink: #2c2f3a;
    --backdrop: #d9d9d9;
  }
  * { box-sizing: border-box; margin: 0; padding: 0; }
  html, body { width: 1200px; height: 800px; overflow: hidden; }
  body {
    background: var(--backdrop);
    display: flex;
    align-items: center;
    justify-content: center;
    gap: 40px;
    font-family: "Work Sans", sans-serif;
  }
  .card {
    position: relative;
    width: 540px;
    height: 309px;
    border-radius: 18px;
    overflow: hidden;
    box-shadow: 0 10px 30px rgba(0,0,0,0.18);
  }

  /* Front */
  .card--front { background: var(--paper); }
  .card__swoosh { position: absolute; left: 0; bottom: 0; width: 100%; height: 100%; }
  .brand-name {
    position: absolute;
    left: 40px;
    top: 34px;
    font-family: "Playfair Display", serif;
    font-weight: 400;
    font-size: 54px;
    color: var(--bronze);
    line-height: 1;
  }
  .divider {
    position: absolute;
    left: 40px;
    right: 40px;
    top: 150px;
    height: 1px;
    background: var(--bronze);
  }
  .contact {
    position: absolute;
    left: 40px;
    top: 166px;
    list-style: none;
    font-size: 13.5px;
    color: var(--ink);
    line-height: 1.55;
  }
  .contact li { display: flex; align-items: center; gap: 8px; }
  .contact svg { width: 10px; height: 10px; flex: none; }
  .person {
    position: absolute;
    right: 40px;
    top: 94px;
    text-align: right;
  }
  .person__name {
    font-family: "Playfair Display", serif;
    font-weight: 700;
    font-size: 25px;
    letter-spacing: 1px;
    color: var(--bronze);
    line-height: 1.1;
  }
  .person__role {
    font-size: 15px;
    color: var(--bronze);
    letter-spacing: 0.5px;
  }

  /* Back */
  .card--back { background: var(--bronze); }
  .back-brand {
    position: absolute;
    right: 48px;
    top: 118px;
    font-family: "Playfair Display", serif;
    font-weight: 400;
    font-size: 58px;
    color: var(--paper);
    line-height: 1;
  }
  .social {
    position: absolute;
    left: 36px;
    top: 142px;
    display: flex;
    flex-direction: column;
    gap: 6px;
    color: var(--paper);
    font-size: 12px;
  }
  .social__networks { display: flex; gap: 14px; }
  .social__network { display: flex; align-items: center; gap: 5px; }
  .social__dot { width: 9px; height: 9px; border-radius: 50%; background: var(--paper); }
  .social__handle { font-weight: 500; font-size: 13px; }
</style>
</head>
<body>

<section class="card card--front" aria-label="Business card front">
  <svg class="card__swoosh" viewBox="0 0 540 309" preserveAspectRatio="none" aria-hidden="true">
    <path d="M0 262 Q200 300 540 300 L540 309 L0 309 Z" fill="var(--bronze)"/>
    <path d="M0 255 Q190 296 540 294" fill="none" stroke="var(--tan)" stroke-width="5"/>
  </svg>

  <div class="brand-name">Lashvera</div>

  <div class="person">
    <div class="person__name">JONAH WHITFIELD</div>
    <div class="person__role">Design Consultant</div>
  </div>

  <div class="divider"></div>

  <ul class="contact">
    <li>
      <svg viewBox="0 0 10 10"><path d="M2 1 L4 1 L4.6 3 L3.4 3.8 Q4.4 5.8 6.2 6.6 L7 5.4 L9 6 L9 8 Q5 9 1 4 Q1 2 2 1 Z" fill="var(--bronze)"/></svg>
      310.555.0142
    </li>
    <li>
      <svg viewBox="0 0 10 10"><rect x="0.5" y="2" width="9" height="6" fill="none" stroke="var(--bronze)"/><path d="M0.5 2 L5 5.5 L9.5 2" fill="none" stroke="var(--bronze)"/></svg>
      hello@lashverastudio.example
    </li>
    <li>
      <svg viewBox="0 0 10 10"><circle cx="5" cy="5" r="4.3" fill="none" stroke="var(--bronze)"/><path d="M0.7 5 H9.3 M5 0.7 Q2.5 5 5 9.3 M5 0.7 Q7.5 5 5 9.3" fill="none" stroke="var(--bronze)" stroke-width="0.8"/></svg>
      www.lashverastudio.example
    </li>
  </ul>
</section>

<section class="card card--back" aria-label="Business card back">
  <div class="social">
    <div class="social__networks">
      <span class="social__network"><span class="social__dot"></span>Snapgrid</span>
      <span class="social__network"><span class="social__dot"></span>Circlebook</span>
    </div>
    <span class="social__handle">@lashverastudiolounge</span>
  </div>
  <div class="back-brand">Lashvera</div>
</section>

</body>
</html>
```